Venture Capital Investment Firm

We are looking to overhaul our existing website (substantially), with only using the same logos (which we can provide).
We are an investment firm that focuses on making loans to late stage technology companies. Our site should ultimately look like other venture capital firms, and look modern and fresh. We have an existing website www.norvellhub.com which this will be replacing, although we will be using a lot of the existing written content, and potentially the numbers of pages we will need, we are not wed to anything else. Please feel free to shoot any questions at any time and thank you in advance for your help!
Websites we like as examples:
https://www.tesmarkfund.com/
https://www.brindlewoodpartners.com/
Target Market(s)
Potential investors who will invest in our firm, as well as potentially companies that are looking to borrow money from us.
Coding
Coded - Design and coding required
Number of Pages Required
5+ page
Colors
Designer to choose colors to be used in the design.
Look and feel

```html
<!DOCTYPE html>
<html lang="en">
<head>
<meta charset="utf-8">
<title>Halvern Crest Investment Partners</title>
<link rel="stylesheet" href="https://fonts.googleapis.com/css2?family=Cinzel:wght@700&family=Montserrat:wght@400;500&family=Oswald:wght@400;500&display=swap">
<style>
:root{
  --navy:#0a0a45;
  --navy-deep:#060633;
  --hero-a:#15166a;
  --hero-b:#3a4aa8;
  --white:#ffffff;
  --panel:#f3f3f5;
  --ink:#0a0a45;
  --body:#6b6b78;
  --muted-white:#d8d9ea;
}
*{margin:0;padding:0;box-sizing:border-box}
html,body{width:1200px;height:3432px;overflow:hidden}
body{position:relative;font-family:"Montserrat",Arial,sans-serif;background:var(--white);color:var(--ink)}
.abs{position:absolute}
.serif{font-family:"Cinzel",Georgia,serif;font-weight:700;letter-spacing:1px}
.btn{position:absolute;display:flex;align-items:center;justify-content:center;border-radius:26px;font-family:"Cinzel",Georgia,serif;font-weight:700;font-size:18px;letter-spacing:.5px;text-decoration:none}
.btn-light{background:var(--white);color:var(--ink)}
.btn-dark{background:var(--navy);color:var(--white)}
.body-text{font-size:14.5px;line-height:27px;color:var(--body)}

/* hero */
.hero{top:0;left:0;width:1200px;height:677px;background:linear-gradient(135deg,var(--navy-deep) 0%,var(--hero-a) 55%,var(--hero-b) 100%)}
.brand{display:flex;align-items:center;gap:12px;color:var(--white);font-family:"Cinzel",Georgia,serif;font-weight:700}
.brand-dot{width:30px;height:30px;border:3px solid var(--white);border-radius:50%}
.nav{top:32px;right:80px;display:flex;gap:26px;font-size:14.5px;color:var(--muted-white);letter-spacing:.5px}
.hero-title{left:78px;top:236px;font-family:"Oswald",Impact,sans-serif;font-weight:500;font-size:40px;line-height:47px;color:var(--white);text-transform:uppercase}
.hero-sub{left:78px;top:386px;font-family:"Oswald",Impact,sans-serif;font-size:18px;color:var(--muted-white);text-transform:uppercase}

/* about */
.about-panel{left:507px;top:815px;width:573px;height:452px;background:var(--panel)}
.about-photo{left:165px;top:757px;width:394px;height:394px;border-radius:50%;background:radial-gradient(circle at 40% 40%,#c9ccd6,#5a6478 70%,#1c2233)}
.section-title{font-size:40px;line-height:47px;color:var(--ink)}
.eyebrow{font-size:16px;line-height:23px;color:var(--ink);font-weight:500;letter-spacing:.3px}

/* strategy */
.strategy{top:1332px;left:0;width:1200px;height:573px;background:var(--panel)}
.icon-circle{width:104px;height:104px;border-radius:50%;background:var(--white);box-shadow:0 6px 14px rgba(10,10,69,.12);display:flex;align-items:center;justify-content:center}
.card-title{font-size:21px;color:var(--ink)}

/* team */
.team{top:1905px;left:0;width:1200px;height:463px;background:var(--navy)}
.team-photo{left:233px;top:2051px;width:333px;height:317px;background:linear-gradient(180deg,#8a8a8a 0%,#4a4a4a 60%,#222 100%);border-radius:160px 160px 0 0}

/* news */
.news-panel{left:161px;top:2552px;width:584px;height:374px;background:var(--panel)}
.news-photo{left:680px;top:2506px;width:364px;height:364px;border-radius:50%;background:radial-gradient(circle at 65% 45%,#8fb3d8,#3b5c86 55%,#1a2a44)}
.dots{top:2951px;left:551px;display:flex;gap:7px}
.dot{width:14px;height:14px;border:1.5px solid var(--ink);border-radius:50%}
.dot.on{background:var(--ink)}

/* footer */
.footer{top:3024px;left:0;width:1200px;height:346px;background:var(--navy);color:var(--muted-white)}
.foot-head{font-size:19px;color:var(--white)}
.foot-text{font-size:14.5px;line-height:27px;color:var(--muted-white)}
.field{width:322px;height:46px;background:#1b1b58;color:var(--muted-white);font-size:14.5px;padding:14px 16px}
.copyright{top:3370px;left:0;width:1200px;height:62px;background:var(--panel);display:flex;align-items:center;justify-content:center;font-size:14.5px;color:var(--body)}
</style>
</head>
<body>

<!-- hero -->
<section class="abs hero" role="img" aria-label="Upward view of glass office towers tinted navy"></section>
<div class="abs brand" style="left:78px;top:24px;font-size:26px"><span class="brand-dot"></span>Halvern Crest</div>
<nav class="abs nav"><span>HOME</span><span>STRATEGY</span><span>ABOUT US</span><span>TEAM</span><span>NEWS</span><span>CONTACT</span><span>INVESTORS</span></nav>
<h1 class="abs hero-title">We are a global structured<br>credit investment firm<br>focused on the</h1>
<p class="abs hero-sub">Healthcare and technology industries</p>
<a class="btn btn-light" style="left:77px;top:441px;width:187px;height:51px">LEARN MORE</a>

<!-- about -->
<div class="abs about-panel"></div>
<div class="abs about-photo" role="img" aria-label="Business presentation in a meeting room with a bar chart on screen"></div>
<h2 class="abs serif section-title" style="left:603px;top:866px">Halvern Crest Started<br>With A Big Idea</h2>
<p class="abs eyebrow" style="left:610px;top:975px;width:400px">FINANCE PROVEN INNOVATION WITH A DIFFERENT APPROACH</p>
<p class="abs body-text" style="left:613px;top:1030px;width:410px">Halvern Crest is a private investment firm unique in its dual focus on life science and technology credit opportunities. Our ambidextrous approach to investing reflects a broad recognition and appreciation for.</p>
<a class="btn btn-dark" style="left:613px;top:1151px;width:183px;height:52px">LEARN MORE</a>

<!-- strategy -->
<section class="abs strategy"></section>
<h2 class="abs serif section-title" style="left:202px;top:1389px">Strategy</h2>
<p class="abs eyebrow" style="left:203px;top:1443px;width:340px">PARTNERS FOR GROWTH INNOVATIVE COMPANIES &amp; THEIR INVESTORS</p>
<p class="abs body-text" style="left:589px;top:1390px;width:470px;color:#4a4a58">Our focus spans the life science and technology industries, two sectors where intellectual property (IP) is an integral driver of asset and enterprise value.</p>

<div class="abs icon-circle" style="left:197px;top:1525px">
  <svg width="58" height="58" viewBox="0 0 58 58" fill="none" stroke="#0a0a45" stroke-width="2">
    <path d="M6 20 Q29 -2 52 20 Z"/><line x1="29" y1="20" x2="29" y2="25"/>
    <circle cx="29" cy="31" r="5"/><circle cx="19" cy="36" r="4"/><circle cx="39" cy="36" r="4"/>
    <path d="M21 52 v-10 a8 8 0 0 1 16 0 v10 Z"/><path d="M12 52 v-7 a7 7 0 0 1 9-5"/><path d="M46 52 v-7 a7 7 0 0 0 -9-5"/>
  </svg>
</div>
<div class="abs icon-circle" style="left:629px;top:1525px">
  <svg width="58" height="58" viewBox="0 0 58 58" fill="none" stroke="#0a0a45" stroke-width="2">
    <circle cx="24" cy="22" r="6"/><circle cx="24" cy="22" r="12"/><circle cx="24" cy="22" r="18"/>
    <path d="M24 22 v18 l-4 -3 -3 3 8 10 h14 l3 -12 -12 -4 v-4 z" fill="#fff"/>
  </svg>
</div>

<h3 class="abs serif card-title" style="left:202px;top:1668px">Life Sciences</h3>
<p class="abs body-text" style="left:202px;top:1705px;width:310px;color:#4a4a58">We have a long track record of partnering with companies and investors that create and commercialize life science products, with extensive experience</p>
<svg class="abs" style="left:203px;top:1829px" width="28" height="16" viewBox="0 0 28 16"><line x1="0" y1="8" x2="22" y2="8" stroke="#0a0a45" stroke-width="3"/><path d="M18 2 L27 8 L18 14 Z" fill="#0a0a45"/></svg>

<h3 class="abs serif card-title" style="left:641px;top:1668px">Technology</h3>
<p class="abs body-text" style="left:641px;top:1705px;width:310px;color:#4a4a58">We uniquely offer sizeable and flexible structured credit financing solutions to innovative technology companies, with a focus on enterprise software</p>
<svg class="abs" style="left:642px;top:1829px" width="28" height="16" viewBox="0 0 28 16"><line x1="0" y1="8" x2="22" y2="8" stroke="#0a0a45" stroke-width="3"/><path d="M18 2 L27 8 L18 14 Z" fill="#0a0a45"/></svg>

<!-- team -->
<section class="abs team"></section>
<h2 class="abs serif" style="left:0;width:1200px;top:1962px;text-align:center;font-size:40px;color:var(--white)">Meet Our Team</h2>
<div class="abs team-photo" role="img" aria-label="Portrait of the managing partner in a dark suit"></div>
<h3 class="abs serif" style="left:645px;top:2053px;font-size:23px;color:var(--white)">Devan Marlowe</h3>
<p class="abs" style="left:647px;top:2088px;font-size:16px;color:var(--white)">Managing Partner</p>
<p class="abs body-text" style="left:647px;top:2131px;width:350px;color:var(--muted-white)">Devan Marlowe leads technology investment origination and evaluation at Halvern Crest. He has over 15 years of technology investment and transaction experience.</p>
<a class="btn btn-light" style="left:646px;top:2252px;width:187px;height:51px">LEARN MORE</a>
<svg class="abs" style="left:32px;top:2120px" width="18" height="40" viewBox="0 0 18 40"><path d="M16 2 L3 20 L16 38" fill="none" stroke="#fff" stroke-width="1.5"/></svg>
<svg class="abs" style="left:1152px;top:2120px" width="18" height="40" viewBox="0 0 18 40"><path d="M2 2 L15 20 L2 38" fill="none" stroke="#fff" stroke-width="1.5"/></svg>

<!-- news -->
<h2 class="abs serif" style="left:0;width:1200px;top:2424px;text-align:center;font-size:40px;color:var(--ink)">Halvern Crest News</h2>
<div class="abs news-panel"></div>
<div class="abs news-photo" role="img" aria-label="Analyst reviewing financial charts on a monitor"></div>
<p class="abs" style="left:222px;top:2620px;font-size:14.5px;color:var(--ink)">April 30, 2018</p>
<h3 class="abs serif" style="left:222px;top:2652px;width:430px;font-size:18.5px;line-height:27px;color:var(--ink)">Halvern Crest Completes Structured Debt Investment in Brightwell</h3>
<p class="abs body-text" style="left:222px;top:2720px;width:410px">Halvern Crest Investment Partners (“Halvern Crest”) announced today that it has completed a structured debt investment in Brightwell, Inc. (“Brightwell”), the leader in employee communication.</p>
<div class="abs serif" style="left:224px;top:2845px;font-size:16px;color:var(--ink);display:flex;align-items:center;gap:8px">READ MORE
  <svg width="24" height="14" viewBox="0 0 24 14"><line x1="0" y1="7" x2="18" y2="7" stroke="#0a0a45" stroke-width="2.5"/><path d="M15 2 L23 7 L15 12 Z" fill="#0a0a45"/></svg></div>
<div class="abs dots"><span class="dot"></span><span class="dot on"></span><span class="dot"></span><span class="dot"></span><span class="dot"></span></div>

<!-- footer -->
<footer class="abs footer"></footer>
<div class="abs brand" style="left:100px;top:3152px;font-size:32px"><span class="brand-dot" style="width:34px;height:34px"></span>Halvern Crest</div>
<a class="abs" style="left:175px;top:3214px;font-size:15px;color:var(--muted-white);text-decoration:underline">Legal Disclaimer</a>

<h4 class="abs serif foot-head" style="left:436px;top:3056px">Contact Us</h4>
<svg class="abs" style="left:434px;top:3108px" width="18" height="26" viewBox="0 0 18 26"><path d="M9 0 a9 9 0 0 1 9 9 c0 7 -9 17 -9 17 s-9-10 -9-17 a9 9 0 0 1 9-9z" fill="#fff"/><circle cx="9" cy="9" r="3.5" fill="#0a0a45"/></svg>
<p class="abs foot-text" style="left:484px;top:3097px">SAN FRANCISCO<br>2150 Alder Lane #318<br>San Francisco, CA  94107</p>
<svg class="abs" style="left:433px;top:3207px" width="22" height="16" viewBox="0 0 22 16"><rect width="22" height="16" rx="1" fill="#fff"/><path d="M1 1 L11 9 L21 1" fill="none" stroke="#0a0a45" stroke-width="1.6"/></svg>
<p class="abs foot-text" style="left:484px;top:3198px;line-height:23px">GENERAL INQUIRIES :<br>inquiries@halverncrest.com</p>
<svg class="abs" style="left:433px;top:3277px" width="22" height="16" viewBox="0 0 22 16"><rect width="22" height="16" rx="1" fill="#fff"/><path d="M1 1 L11 9 L21 1" fill="none" stroke="#0a0a45" stroke-width="1.6"/></svg>
<p class="abs foot-text" style="left:484px;top:3269px;line-height:23px">MEDIA INQUIRIES :<br>media@halverncrest.com</p>

<h4 class="abs serif foot-head" style="left:793px;top:3056px">Newsletter</h4>
<p class="abs foot-text" style="left:793px;top:3097px;width:330px">Would you like to receive our exclusive news and update for signup our newsletter !</p>
<div class="abs field" style="left:791px;top:3165px">Enter Name *</div>
<div class="abs field" style="left:791px;top:3220px">Enter Email *</div>
<a class="btn btn-light" style="left:791px;top:3275px;width:160px;height:51px">SUBSCRIBE</a>

<div class="abs copyright">©2019 Halvern Crest Investment Partners LLC.&nbsp; All Rights Reserved.</div>

</body>
</html>
```